Baby Organic Coconut Body Lotion

Meadow Hush Naturals is developing a line of Organic and Natural skin care products for babies and toddlers, although our skin care can also be used by adults too. These products include a body lotion, shampoo & body wash, powder, hair cream, massage body oil, bath soak, baby balm, Bar Soap, gift box and many more.
This will be an ever expanding line so the list will go on and on. We are looking forward for an eye catching designs. I attached some of our current label designs and product images. Also, we have different Baby organic body lotion and Baby organic shampoo & body wash with different fruit flavours. Coconut lotion will share the same design with the shampoo & body wash. I would like you to start with the coconut design. I have uploaded plastic bottles with different colourful caps. The bottle with the white cap is for the coconut design. the bottle with the red cap is for the strawberry design. the bottle with the orange cap is for the orange design. the bottle with the yellow cap is for the pineapple design. the bottle with the green cap is for the apple design. Bear in my mind that my baby organic skin care are made with different fruit flavours.
Target Market(s)
My target market are for mothers that wants to buy there baby and toddler skin care products.
Industry/Entity Type
Baby
Look and feel

```html
<!DOCTYPE html>
<html lang="en">
<head>
<meta charset="utf-8">
<title>Meadow Hush Naturals – Baby Organic Coconut Body Lotion Labels</title>
<link href="https://fonts.googleapis.com/css2?family=Saira+Condensed:wght@400;500&family=Varela+Round&family=Kanit:wght@400;500&display=swap" rel="stylesheet">
<style>
  :root{
    --page:#e8e6e1;
    --label:#fbfbf8;
    --gold:#ad9b35;
    --gold-text:#b09e3c;
    --gold-band:#a99834;
    --gold-band-light:#c3b45a;
    --ink-soft:#b8a84e;
    --coconut-flesh:#f7f3ea;
    --coconut-shell:#8a5a36;
    --coconut-husk:#b98a5c;
    --palm:#8fb0a0;
  }
  *{box-sizing:border-box;margin:0;padding:0}
  html,body{width:1200px;height:1200px;overflow:hidden;background:var(--page)}
  .canvas{width:1200px;height:1200px;position:relative;display:flex;justify-content:center;align-items:center;gap:44px}

  /* Back label */
  .label-back{width:440px;height:860px;background:var(--label);display:flex;flex-direction:column;
    font-family:"Kanit",sans-serif;color:var(--gold-text);text-align:center;box-shadow:0 2px 10px rgba(0,0,0,.08)}
  .back-copy{padding:30px 26px 0}
  .back-copy p{font-size:17px;line-height:1.32;margin-bottom:24px}
  .back-copy strong{font-weight:500}
  .product-band{background:var(--gold-band);color:#fff;font-weight:500;font-size:18px;padding:14px 10px;letter-spacing:-.2px;margin-top:2px}
  .ingredients{margin:14px 10px 0;border:2px solid var(--gold-band);padding:8px 10px;font-family:"Varela Round",sans-serif;font-size:9.6px;line-height:1.5;color:var(--ink-soft)}
  .ingredients h3{font-size:10px;font-weight:400;margin-bottom:8px}
  .maker{font-family:"Varela Round",sans-serif;font-size:12px;line-height:1.45;color:var(--ink-soft);padding:12px 30px 0}
  .free-from{font-family:"Varela Round",sans-serif;font-size:12px;color:var(--ink-soft);margin-top:20px}
  .contact-band{margin-top:auto;background:linear-gradient(90deg,var(--gold-band),var(--gold-band-light),var(--gold-band));color:#fff;
    font-size:15px;font-weight:500;padding:18px 16px;display:flex;justify-content:center;gap:14px;white-space:nowrap}

  /* Front label */
  .label-front{width:420px;height:860px;background:var(--label);display:flex;flex-direction:column;
    font-family:"Saira Condensed",sans-serif;color:var(--gold-text);text-align:center;box-shadow:0 2px 10px rgba(0,0,0,.08)}
  .brand{height:230px;display:flex;align-items:center;justify-content:center;gap:12px;padding-top:10px}
  .brand-dot{width:16px;height:16px;border-radius:50%;background:var(--gold)}
  .brand-name{font-weight:500;font-size:50px;line-height:.95;color:var(--gold);text-align:left}
  .product-title{font-size:46px;font-weight:400;line-height:1.34;padding:22px 0 26px}
  .feature-band{background:var(--gold-band);color:#fff;font-size:25px;line-height:1.35;padding:4px 0 6px}
  .tested{font-size:21px;margin-top:8px}
  .fruit-photo{position:relative;margin-top:auto;height:380px;
    background:linear-gradient(125deg,var(--label) 0%,var(--coconut-flesh) 18%,var(--coconut-husk) 42%,var(--coconut-shell) 60%,var(--palm) 82%,var(--label) 98%)}
  .photo-footer{position:absolute;left:0;right:0;bottom:0;height:78px;
    background:linear-gradient(90deg,rgba(169,152,52,.9),rgba(230,210,80,.55),rgba(169,152,52,.85));
    display:flex;justify-content:space-between;align-items:center;padding:0 24px;color:#fff;font-size:30px}
</style>
</head>
<body>
<main class="canvas">

  <section class="label-back" aria-label="Back label">
    <div class="back-copy">
      <p><strong>BABY ORGANIC COCONUT BODY LOTION:</strong> Meadow Hush Naturals only use the kindest ingredients to care for delicate skin. A blend of organic coconut, avocado and jojoba oils work together to provide deep moisturising for your baby's dry and sensitive skin.</p>
      <p><strong>SAFETY:</strong> For external use only. Avoid contact with eyes. If contact with eyes occurs, rinse well with water immediately. Keep out of reach from children. Seek medical attention if swallowed. Store in a cool dry place.</p>
      <p><strong>DIRECTIONS FOR USE:</strong> Apply a small amount of lotion when the skin is dry or after bath with Meadow Hush Naturals Baby Shampoo &amp; Body Wash.</p>
    </div>
    <div class="product-band">BABY ORGANIC COCONUT BODY LOTION</div>
    <div class="ingredients">
      <h3>Ingredients:</h3>
      Water (aqua)**, Aloe Barbadensis leaf juice**, organic rosemary floral water*, organic chamomile floral water*, organic coconut oil*, organic avocado butter*, organic jojoba oil*, organic sunflower oil*, organic glycerin*, organic sweet almond oil*, vegetable emulsifiers*, organic cocoa butter*, organic shea butter*, xanthan gum**, citric acid**, sodium benzoate &amp; potassium sorbate (preservative)**. *Certified organic ingredients **Natural ingredients
    </div>
    <p class="maker">Made in England For Little Orchard Kids. Meadow Hush Naturals is a registered trademark of: Little Orchard Kids, Unit 4, Larkfield Court, Mill Lane, Kent, UK, ME9 2TP.</p>
    <p class="free-from">No Parabens, No SLS.</p>
    <div class="contact-band"><span>www.littleorchardkids.com</span><span>hello@littleorchardkids.com</span></div>
  </section>

  <section class="label-front" aria-label="Front label">
    <div class="brand">
      <span class="brand-dot"></span>
      <span class="brand-name">Meadow Hush<br>Naturals</span>
    </div>
    <h1 class="product-title">Baby Organic<br>Coconut Body Lotion</h1>
    <div class="feature-band">with organic coconut,<br>avocado &amp; jojoba</div>
    <p class="tested">Dermatologically tested</p>
    <div class="fruit-photo" role="img" aria-label="Photograph of a halved coconut with white flesh and brown shell beside palm leaves">
      <div class="photo-footer"><span>80% organic</span><span>125ml e</span></div>
    </div>
  </section>

</main>
</body>
</html>
```